Oil and Gas Exploration and Production company needs a business card design

We need a business card design using our logo and colors in the logo. We want a mainstream design.

```html
<!DOCTYPE html>
<html lang="en">
<head>
<meta charset="utf-8">
<title>Sunvale Oil &amp; Gas — Business Card</title>
<link rel="stylesheet" href="https://fonts.googleapis.com/css2?family=Roboto+Slab:wght@400;700&family=Roboto:wght@400&display=swap">
<style>
  :root {
    --ink: #111111;
    --gold: #d3a02c;
    --gold-deep: #b5861f;
    --paper: #ffffff;
    --grey-text: #3a3a3a;
    --stage: #e9e7e3;
  }
  * { box-sizing: border-box; margin: 0; padding: 0; }
  html, body {
    width: 1200px; height: 911px; overflow: hidden;
    background: var(--stage);
  }
  .canvas {
    width: 1200px; height: 911px;
    display: flex; align-items: center; justify-content: center; gap: 60px;
  }
  .card {
    width: 520px; height: 297px;
    border-radius: 22px;
    position: relative; overflow: hidden;
    box-shadow: 0 6px 18px rgba(0,0,0,0.18);
  }

  /* Front face */
  .card--front { background: var(--ink); }
  .front__burst {
    position: absolute; inset: 0;
    background: radial-gradient(circle at 50% 50%, var(--gold) 0%, var(--gold-deep) 38%, #4a3710 60%, var(--ink) 82%);
  }
  .front__panel {
    position: absolute; left: 50%; top: 50%;
    width: 200px; height: 200px; margin: -100px 0 0 -100px;
    border-radius: 50%;
    background: var(--paper);
    display: flex; flex-direction: column; align-items: center; justify-content: center;
    text-align: center;
    font-family: "Roboto Slab", Georgia, serif;
  }
  .front__dot {
    width: 14px; height: 14px; border-radius: 50%;
    background: var(--ink); margin-bottom: 8px;
  }
  .front__name {
    font-weight: 700; font-size: 17px; letter-spacing: 0.5px;
    color: var(--ink); text-transform: uppercase;
  }
  .front__title {
    font-weight: 400; font-size: 12px; letter-spacing: 0.5px;
    color: var(--gold); text-transform: uppercase; margin: 2px 0 10px;
  }
  .front__contact {
    list-style: none;
    font-size: 10.5px; line-height: 1.55; color: var(--grey-text);
  }

  /* Back face */
  .card--back { background: var(--paper); }
  .back__site {
    position: absolute; left: 34px; top: 50%;
    transform: translate(-50%, -50%) rotate(90deg) translateY(-8px);
    font-family: "Roboto", Arial, sans-serif;
    font-size: 10px; letter-spacing: 5px; color: var(--grey-text);
    white-space: nowrap;
  }
  .back__brand {
    position: absolute; left: 50%; top: 50%;
    transform: translate(-44%, -50%);
    display: flex; align-items: center; gap: 14px;
  }
  .back__mark {
    width: 34px; height: 34px; border-radius: 50%;
    background: var(--ink); flex: none;
  }
  .back__name {
    font-family: "Roboto Slab", Georgia, serif;
    font-weight: 700; font-size: 40px; line-height: 1.05;
    color: var(--ink);
  }
</style>
</head>
<body>
  <main class="canvas">
    <section class="card card--front" aria-label="Card front">
      <div class="front__burst" role="img" aria-label="Gold sunburst rays radiating on black"></div>
      <div class="front__panel">
        <span class="front__dot"></span>
        <h1 class="front__name">Daniel Reyes</h1>
        <p class="front__title">CEO/Founder</p>
        <ul class="front__contact">
          <li>555 014 2290</li>
          <li>info@sunvaleoil.com</li>
          <li>www.sunvaleoil.com</li>
        </ul>
      </div>
    </section>

    <section class="card card--back" aria-label="Card back">
      <p class="back__site">www.sunvaleoil.com</p>
      <div class="back__brand">
        <span class="back__mark"></span>
        <p class="back__name">Sunvale<br>Oil &amp; Gas</p>
      </div>
    </section>
  </main>
</body>
</html>
```